Business Card Design for Occupational Medicine Start Up Company

We need to design a professional business card. We are a healthcare company providing occupational medicine services to blue collar industries. We are professional, efficient and high quality service providers.

Target Market(s)

Blue Collar Industry: Shipbuilding, Ports, Trucking Companies; The Executives and Safety Officers for these companies

Industry/Entity Type

Healthcare

Contact Information for Business Card

Logo, Name, Title, Email, Phone

Other font styles liked:
• Please match our Brand Guide

Requirements
Must have
• Our Company Colors and Logo

```html
<!DOCTYPE html>
<html lang="en">
<head>
<meta charset="utf-8">
<title>Shiftwell Clinics – Business Card</title>
<link href="https://fonts.googleapis.com/css2?family=Arimo:wght@400;700&display=swap" rel="stylesheet">
<style>
  :root {
    --stage: #2f2f2f;
    --navy: #2b3580;
    --amber: #f5b253;
    --white: #ffffff;
    --paper: #eeeced;
  }
  html, body {
    margin: 0;
    padding: 0;
    width: 1075px;
    height: 1200px;
    overflow: hidden;
    background: var(--stage);
    font-family: "Arimo", Arial, sans-serif;
  }
  .card {
    position: absolute;
    width: 663px;
    height: 394px;
    overflow: hidden;
  }
  .card--front {
    left: 206px;
    top: 187px;
    background: var(--navy);
    color: var(--white);
  }
  .card--back {
    left: 203px;
    top: 637px;
    background: var(--paper);
  }
  .brand-panel {
    position: absolute;
    inset: 0;
  }
  .holder {
    position: absolute;
    left: 30px;
    top: 182px;
  }
  .holder__name {
    margin: 0;
    font-size: 23px;
    font-weight: 700;
    letter-spacing: 0.2px;
    line-height: 1.1;
  }
  .holder__title {
    margin: 2px 0 0;
    font-size: 17.5px;
    font-weight: 400;
  }
  .contact {
    position: absolute;
    left: 30px;
    top: 273px;
    margin: 0;
    padding: 0;
    list-style: none;
    font-size: 17.5px;
  }
  .contact__item {
    display: flex;
    align-items: center;
    gap: 6px;
    height: 23.5px;
  }
  .contact__icon {
    width: 17px;
    height: 17px;
    flex: none;
  }
  .wordmark {
    position: absolute;
    left: 0;
    right: 0;
    top: 92px;
    display: flex;
    flex-direction: column;
    align-items: center;
    gap: 36px;
  }
  .wordmark__dot {
    width: 64px;
    height: 64px;
    border-radius: 50%;
    background: var(--navy);
  }
  .wordmark__name {
    margin: 0;
    font-size: 40px;
    font-weight: 700;
    color: var(--navy);
    letter-spacing: 0.5px;
  }
</style>
</head>
<body>

<section class="card card--front">
  <svg class="brand-panel" viewBox="0 0 663 394" role="img" aria-label="Large brand symbol decoration in white on amber">
    <path d="M356 0 C 290 20 250 70 252 120 C 255 200 340 320 437 394 L663 394 L663 0 Z" fill="var(--amber)"/>
  </svg>

  <div class="holder">
    <h1 class="holder__name">DANIEL REYES</h1>
    <p class="holder__title">Managing Director</p>
  </div>

  <ul class="contact">
    <li class="contact__item">
      <svg class="contact__icon" viewBox="0 0 24 24" fill="none" stroke="currentColor" stroke-width="2.2" stroke-linecap="round" stroke-linejoin="round">
        <path d="M5 3h4l2 5-2.5 1.5a11 11 0 0 0 6 6L16 13l5 2v4a2 2 0 0 1-2 2A17 17 0 0 1 3 5a2 2 0 0 1 2-2z"/>
        <path d="M15 3a6 6 0 0 1 6 6M15 7a2 2 0 0 1 2 2"/>
      </svg>
      <span>044-555 210 386</span>
    </li>
    <li class="contact__item">
      <svg class="contact__icon" viewBox="0 0 24 24" fill="none" stroke="currentColor" stroke-width="2.2" stroke-linejoin="round">
        <rect x="2" y="5" width="20" height="14"/>
        <path d="M2 5l10 8 10-8M2 19l7-7M22 19l-7-7"/>
      </svg>
      <span>hello@shiftwell.com</span>
    </li>
    <li class="contact__item">
      <svg class="contact__icon" viewBox="0 0 24 24" fill="none" stroke="currentColor" stroke-width="2">
        <circle cx="12" cy="12" r="10"/>
        <ellipse cx="12" cy="12" rx="4.5" ry="10"/>
        <path d="M2 12h20M4 6.5h16M4 17.5h16"/>
      </svg>
      <span>www.shiftwellclinics.com</span>
    </li>
  </ul>
</section>

<section class="card card--back">
  <div class="wordmark">
    <div class="wordmark__dot"></div>
    <p class="wordmark__name">SHIFTWELL CLINICS</p>
  </div>
</section>

</body>
</html>
```